Simple and Clean business card design

We would like the design to be simple clean and to incorporate our colors.

We are open to your design and talent, we have the dots in our logo as we think of it as data points and we connect data points for people.

We are open to see the great creative and clean design you bring to the table

Contact Information for Business Card

please include: name, position, email, phone and website

Font styles to use
Sans Serif

Requirements
Must have
• my colors incorporated, simplicity
Nice to have
• lots of white space, simplicity
Should not have
• complexicity/ complex art

```html
<!DOCTYPE html>
<html lang="en">
<head>
<meta charset="utf-8">
<title>Nodera Business Card</title>
<link rel="stylesheet" href="https://fonts.googleapis.com/css2?family=Montserrat:wght@600&family=Work+Sans:wght@400;500&display=swap">
<style>
  :root {
    --backdrop: #161616;
    --card: #262626;
    --card-edge: #5a80cf;
    --accent-blue: #5a80cf;
    --text-light: #f2f2f2;
    --logo-muted: #8c8c8c;
  }
  * { box-sizing: border-box; margin: 0; padding: 0; }
  html, body {
    width: 1200px; height: 900px; overflow: hidden;
    background: var(--backdrop);
  }
  .canvas {
    width: 1200px; height: 900px;
    display: flex; flex-direction: column; align-items: center; justify-content: center;
    gap: 40px;
  }
  .card {
    width: 700px; height: 400px;
    background: var(--card);
    border-bottom: 6px solid var(--card-edge);
    position: relative;
    display: flex; align-items: center;
  }
  .card--front { justify-content: center; }
  .wordmark {
    font-family: "Work Sans", sans-serif; font-weight: 500;
    letter-spacing: -1px; line-height: 1; white-space: nowrap;
  }
  .card--front .wordmark { font-size: 96px; color: var(--logo-muted); }
  .card--back { padding: 0 0 0 56px; }
  .card--back .wordmark { font-size: 72px; color: var(--text-light); width: 290px; }
  .divider {
    width: 2px; height: 190px; background: var(--accent-blue);
    margin: 0 36px 0 20px; flex: none;
  }
  .contact { font-family: "Work Sans", sans-serif; color: var(--text-light); font-size: 17px; line-height: 1.45; }
  .contact__name {
    font-family: "Montserrat", sans-serif; font-weight: 600;
    color: var(--accent-blue); font-size: 24px; letter-spacing: 2.5px;
    text-transform: uppercase; line-height: 1.1;
  }
  .contact__role { font-size: 18px; margin-bottom: 14px; }
  .contact__address { margin-bottom: 10px; }
  .contact__line { display: flex; align-items: center; gap: 8px; }
  .contact__icon { width: 13px; height: 13px; flex: none; }
</style>
</head>
<body>
<main class="canvas">
  <section class="card card--front">
    <div class="wordmark">Nodera</div>
  </section>

  <section class="card card--back">
    <div class="wordmark">Nodera</div>
    <div class="divider"></div>
    <div class="contact">
      <p class="contact__name">Daniel Reyes</p>
      <p class="contact__role">Founder</p>
      <p class="contact__address">418 Linden Park Road<br>Marlow, TX 78600</p>
      <p class="contact__line">
        <svg class="contact__icon" viewBox="0 0 16 16" fill="none" stroke="#5a80cf" stroke-width="1.6"><path d="M4 1.5 6.5 4.5 5 6.5q1.5 3 4.5 4.5l2-1.5 3 2.5-1.5 2.5Q7 14 2 8 1 5 4 1.5z"/></svg>
        0412 555 019
      </p>
      <p class="contact__line">
        <svg class="contact__icon" viewBox="0 0 16 16" fill="none" stroke="#5a80cf" stroke-width="1.4"><rect x="1.5" y="3.5" width="13" height="9" rx="1"/><path d="M1.5 4 8 9l6.5-5"/></svg>
        hello@noderadata.com
      </p>
      <p class="contact__line">
        <svg class="contact__icon" viewBox="0 0 16 16" fill="none" stroke="#5a80cf" stroke-width="1.2"><circle cx="8" cy="8" r="6.5"/><ellipse cx="8" cy="8" rx="3" ry="6.5"/><path d="M1.5 8h13M2.5 4.8h11M2.5 11.2h11"/></svg>
        www.noderadata.com
      </p>
    </div>
  </section>
</main>
</body>
</html>
```